IT solutions & services company requires stationary makeover

Looking for a consistent modern, professional design across our printed client touch points:
Business Cards
Letterhead
Client proposal
Flyer
Postcard

We provide solutions for SME IT - servers, backups, AV etc, and the ongoing services around them.
we are happy with our logo - please see attached and would like the colour theme to be maintained.

```html
<!DOCTYPE html>
<html lang="en">
<head>
<meta charset="utf-8">
<title>Nexa Business Cards</title>
<link rel="stylesheet" href="https://fonts.googleapis.com/css2?family=Arimo:ital,wght@0,400;0,700;1,400&display=swap">
<style>
  :root {
    --bg: #ecebe8;
    --brand-blue: #1ba7e1;
    --brand-deep: #1b7fa6;
    --ink: #3a3a3a;
    --ink-soft: #555555;
    --paper: #ffffff;
  }
  * { box-sizing: border-box; margin: 0; padding: 0; }
  html, body {
    width: 1200px; height: 801px; overflow: hidden;
    background: var(--bg);
    font-family: "Arimo", Arial, sans-serif;
  }
  .stage {
    width: 1200px; height: 801px;
    display: flex; align-items: center; justify-content: center; gap: 60px;
  }
  .card {
    position: relative; width: 490px; height: 280px;
    box-shadow: 0 6px 18px rgba(0,0,0,.18);
    overflow: hidden;
  }
  .brand-name {
    font-weight: 400; color: var(--ink);
    line-height: 1; white-space: nowrap;
  }

  /* Front */
  .card--front {
    background: var(--brand-blue);
    display: flex; align-items: center; justify-content: center;
  }
  .card--front .brand-name { font-size: 48px; }

  /* Back */
  .card--back { background: var(--paper); }
  .card__band {
    position: absolute; left: 40px; top: 0; bottom: 0; width: 190px;
    background: var(--brand-blue);
    display: flex; align-items: center; justify-content: center;
  }
  .card__band .brand-name { font-size: 36px; }
  .person {
    position: absolute; right: 22px; top: 30px; text-align: right;
  }
  .person__name { font-size: 25px; color: var(--brand-deep); }
  .person__role { font-size: 12px; font-style: italic; color: var(--ink-soft); margin-top: 2px; }
  .contact {
    position: absolute; right: 22px; bottom: 22px; text-align: right;
    font-size: 10.5px; line-height: 1.45; color: var(--ink-soft);
    font-style: normal;
  }
  .contact__web { color: var(--brand-deep); font-weight: 700; font-size: 11px; }
</style>
</head>
<body>
<main class="stage">
  <section class="card card--front" aria-label="Business card front">
    <span class="brand-name">Nexa</span>
  </section>

  <section class="card card--back" aria-label="Business card back">
    <div class="card__band">
      <span class="brand-name">Nexa</span>
    </div>
    <div class="person">
      <p class="person__name">Daniel Rowe</p>
      <p class="person__role">chief executive officer</p>
    </div>
    <address class="contact">
      03 555 0182<br>
      drowe@nexa-it.example<br>
      Level 2,<br>
      Harbour Lane,<br>
      Lyttelton, NZ<br>
      <span class="contact__web">www.nexa-it.example</span>
    </address>
  </section>
</main>
</body>
</html>
```